Podiatry Clinic needs an A0 poster design

we need an A0 poster design for our clinic frontage to include our logo and a feet theme. it is located either in a frame on a glass wall, or in a freestanding poster holder within a shopping centre.
Our clinic values are integrity, respect, excellence, happiness and fun.
We want to let people know that if your feet fail you, then the rest of you slows down very quickly, so get your feet checked immediately. we deal with kids feet, sporty feet, mature feet.

Target Market(s)

parents with kids

Industry/Entity Type

Medical

Requirements
Must have
• Bramblewick Health Logo
• www.bramblewickhealth.net
• 6172 0918
• easy to read from a distance
Nice to have
• fun, friendly, inviting, colourful, happy.
Should not have
• cartoon
• ugly
• sad
• not too much text
• no fanciful fonts

```html
<!DOCTYPE html>
<html lang="en">
<head>
<meta charset="utf-8">
<title>Bramblewick Health – Foot Problems Solved</title>
<link rel="stylesheet" href="https://fonts.googleapis.com/css2?family=Anton&family=Roboto+Condensed:wght@700;900&family=Kaushan+Script&display=swap">
<style>
  :root {
    --orange: #f0682a;
    --blue: #3b5ea9;
    --white: #ffffff;
    --black: #111111;
    --skin-light: #f3cdb4;
    --skin-mid: #e0a585;
    --skin-deep: #c98463;
    --logo-blue: #2f56a3;
  }
  html, body {
    margin: 0;
    padding: 0;
    overflow: hidden;
    background: #ffffff;
  }
  .poster {
    position: relative;
    width: 857px;
    height: 1200px;
    overflow: hidden;
    background: var(--white);
    font-family: "Roboto Condensed", Arial, sans-serif;
  }
  .top-band {
    position: absolute;
    left: 0; top: 0;
    width: 857px; height: 686px;
    background: var(--orange);
  }
  .headline {
    position: absolute;
    left: 0; top: 22px;
    width: 857px;
    margin: 0;
    text-align: center;
    font-family: "Anton", Impact, sans-serif;
    font-weight: 400;
    font-size: 128px;
    line-height: 130px;
    letter-spacing: 2px;
    color: var(--white);
    -webkit-text-stroke: 8px var(--black);
    paint-order: stroke fill;
    text-shadow: 4px 5px 0 rgba(0,0,0,0.35);
  }
  .services {
    position: absolute;
    left: 0; top: 422px;
    width: 857px;
    margin: 0;
    text-align: center;
    font-weight: 700;
    font-size: 33px;
    color: var(--white);
    word-spacing: 2px;
  }
  .walk-ins {
    position: absolute;
    left: 0; top: 458px;
    width: 857px;
    margin: 0;
    text-align: center;
    font-weight: 900;
    font-size: 62px;
    color: var(--white);
  }
  .limp-ins {
    position: absolute;
    left: 95px; top: 580px;
    padding: 4px 34px 10px 26px;
    background: var(--black);
    color: var(--white);
    font-family: "Kaushan Script", "Roboto Condensed", sans-serif;
    font-size: 64px;
    line-height: 72px;
    transform: rotate(-5deg);
    transform-origin: left center;
    z-index: 3;
  }
  .feet-photo {
    position: absolute;
    left: 170px; top: 660px;
    width: 687px; height: 325px;
    background:
      radial-gradient(ellipse at 40% 60%, var(--skin-mid) 0%, transparent 55%),
      linear-gradient(160deg, var(--skin-light) 0%, var(--skin-mid) 55%, var(--skin-deep) 100%);
    -webkit-mask-image: linear-gradient(to bottom, transparent 0%, #000 18%);
    mask-image: linear-gradient(to bottom, transparent 0%, #000 18%);
    z-index: 1;
  }
  .brand {
    position: absolute;
    left: 20px; top: 730px;
    width: 240px;
    text-align: center;
    z-index: 2;
  }
  .brand-dot {
    display: block;
    width: 170px; height: 170px;
    margin: 0 auto 12px;
    border-radius: 50%;
    background: var(--logo-blue);
  }
  .brand-name {
    font-weight: 700;
    font-size: 34px;
    line-height: 36px;
    color: var(--logo-blue);
  }
  .bottom-band {
    position: absolute;
    left: 0; top: 985px;
    width: 857px; height: 215px;
    background: var(--blue);
  }
  .team-photo {
    position: absolute;
    left: 585px; top: 975px;
    width: 172px; height: 120px;
    background: linear-gradient(180deg, #d8cfc2 0%, #b98a74 50%, #5e8a4c 100%);
    border: 3px solid var(--white);
    box-sizing: border-box;
    z-index: 2;
  }
  .phone {
    position: absolute;
    left: 38px; top: 1010px;
    display: flex;
    align-items: center;
    gap: 14px;
    margin: 0;
    font-weight: 700;
    font-size: 58px;
    color: var(--white);
  }
  .phone svg { width: 44px; height: 44px; }
  .web {
    position: absolute;
    left: 0; top: 1092px;
    width: 857px;
    margin: 0;
    text-align: center;
    font-weight: 700;
    font-size: 64px;
    color: var(--white);
  }
</style>
</head>
<body>
<main class="poster">
  <div class="top-band"></div>

  <h1 class="headline">FOOT<br>PROBLEMS<br>SOLVED!</h1>
  <p class="services">• Kids Feet &nbsp;• Sporty Feet &nbsp;• Mature Feet</p>
  <p class="walk-ins">Walk-ins welcome</p>
  <div class="limp-ins">Limp-ins too!</div>

  <div class="feet-photo" role="img" aria-label="Photo of many bare feet of children and adults raised together"></div>

  <div class="brand">
    <span class="brand-dot"></span>
    <div class="brand-name">Bramblewick Health</div>
  </div>

  <div class="bottom-band"></div>
  <div class="team-photo" role="img" aria-label="Photo of the clinic team standing together"></div>

  <p class="phone">
    <svg viewBox="0 0 24 24" aria-hidden="true">
      <circle cx="12" cy="12" r="12" fill="#ffffff"/>
      <path fill="#3b5ea9" d="M8.2 5.5c.4-.3 1-.2 1.3.2l1.4 2.2c.3.4.2 1-.2 1.3l-.9.7c.6 1.4 1.8 2.7 3.2 3.4l.7-.9c.3-.4.9-.5 1.3-.2l2.2 1.4c.4.3.5.9.2 1.3l-.9 1.3c-.5.7-1.4 1-2.2.7C10.6 15.8 8 13.2 6.7 9.5c-.3-.8 0-1.7.7-2.2z"/>
    </svg>
    6172 0918
  </p>
  <p class="web">www.bramblewickhealth.net</p>
</main>
</body>
</html>
```